Young, dynamic furniture company needs a new business card design

We require a new business card design for our modern furniture company which supplies furniture and appliances to the property and development market.
Oakridge Interiors has become one of the leading furniture & appliance suppliers to the property market withing London. With over 10 years experience, we have increased our business to supply not only private landlords and managing agents, but also property developers, housing associations and local councils.
We offer not only a complete range of furniture which includes beds, wardrobes, dining sets and sofas, but also a high quality, full delivery and assembly service to help you with all our furnishing needs.

Target Market(s)

Private landlords, estate agents, letting agents, property management companies

Industry/Entity Type

Business

Contact Information for Business Card

Name,
Title,
Address,
Mobile,
Telephone,
Fax, Website, email address

Font styles to use
Sans Serif

Colors
3176b5
0555a3
85abd2
cfdeed

Requirements
Must have
• All the above information for each of our staff, along with our logo

```html
<!DOCTYPE html>
<html lang="en">
<head>
<meta charset="utf-8">
<title>Oakridge Interiors – Business Card</title>
<link href="https://fonts.googleapis.com/css2?family=Roboto+Condensed:wght@400;700&display=swap" rel="stylesheet">
<style>
  :root{
    --page:#e9e9eb;
    --card:#141619;
    --ink:#f2f2f2;
    --muted:#8b8f96;
    --brand:#3176b5;
    --brand-deep:#0555a3;
    --brand-soft:#85abd2;
    --rule:#5a5e64;
  }
  *{margin:0;padding:0;box-sizing:border-box}
  html,body{width:1200px;height:864px;overflow:hidden}
  body{
    background:var(--page);
    font-family:"Roboto Condensed",Arial,sans-serif;
    display:flex;flex-direction:column;align-items:center;justify-content:center;gap:56px;
  }
  .card{
    position:relative;width:630px;height:360px;background:var(--card);
    box-shadow:0 6px 18px rgba(0,0,0,.25);
  }
  /* back */
  .card--back{display:flex;flex-direction:column;align-items:center;justify-content:center;gap:26px}
  .brand{display:flex;align-items:center;gap:12px}
  .brand__mark{width:22px;height:22px;background:var(--brand)}
  .brand__name{font-weight:700;color:var(--ink);letter-spacing:.04em;text-transform:uppercase}
  .card--back .brand__name{font-size:30px}
  .tagline{color:var(--muted);font-size:17px;text-align:center;line-height:1.35}

  /* front */
  .person{position:absolute;left:44px;top:58px;color:var(--brand);text-transform:uppercase}
  .person__name{font-size:23px;letter-spacing:.03em}
  .person__title{font-size:16px;margin-top:2px;letter-spacing:.03em}
  .rule{position:absolute;height:1px;background:var(--rule)}
  .rule--top{left:150px;top:110px;width:250px}
  .rule--brand{left:400px;top:244px;width:190px}
  .contacts{position:absolute;left:44px;top:128px;list-style:none}
  .contacts li{display:flex;align-items:center;gap:12px;color:var(--ink);font-size:16px;height:25px}
  .contacts svg{width:14px;height:14px;fill:var(--brand)}
  .front-brand{position:absolute;right:40px;top:168px;text-align:right}
  .front-brand .brand{justify-content:flex-end}
  .front-brand .brand__name{font-size:22px}
  .front-brand .brand__sub{color:var(--ink);font-size:10.5px;letter-spacing:.08em;text-transform:uppercase;margin-top:3px}
  .address{position:absolute;right:40px;top:262px;text-align:right;color:var(--ink);font-size:16px;line-height:1.45}
  .address__web{letter-spacing:.12em}
</style>
</head>
<body>

<section class="card card--back">
  <div class="brand">
    <span class="brand__mark"></span>
    <span class="brand__name">Oakridge Interiors</span>
  </div>
  <p class="tagline">High quality, full delivery &amp; assembly<br>service to help you with all our furnishing needs.</p>
</section>

<section class="card card--front">
  <div class="person">
    <p class="person__name">Daniel Marsh</p>
    <p class="person__title">President</p>
  </div>
  <div class="rule rule--top"></div>

  <ul class="contacts">
    <li><svg viewBox="0 0 16 16"><path d="M3 1h3l1.5 4-2 1.2a9 9 0 0 0 4.3 4.3L11 8.5l4 1.5v3a2 2 0 0 1-2 2A12 12 0 0 1 1 3a2 2 0 0 1 2-2z"/></svg>020 7946 0158</li>
    <li><svg viewBox="0 0 16 16"><path d="M4 0h8a1 1 0 0 1 1 1v14a1 1 0 0 1-1 1H4a1 1 0 0 1-1-1V1a1 1 0 0 1 1-1zm1 2v10h6V2zm3 11a1 1 0 1 0 0 2 1 1 0 0 0 0-2z"/></svg>07700 900 482</li>
    <li><svg viewBox="0 0 16 16"><path d="M4 1h6l2 2v3H4zM1 7h14v7H1zm3 2v1h2V9zm4 0v1h2V9zm-4 2v1h2v-1zm4 0v1h2v-1z"/></svg>020 7946 0273</li>
    <li><svg viewBox="0 0 16 16"><path d="M1 3h14v10H1zm1.5 1.5L8 9l5.5-4.5z"/></svg>daniel@oakridgeinteriors.co.uk</li>
  </ul>

  <div class="front-brand">
    <div class="brand">
      <span class="brand__mark"></span>
      <span class="brand__name">Oakridge Interiors</span>
    </div>
    <p class="brand__sub">Trade Furniture Solutions</p>
  </div>
  <div class="rule rule--brand"></div>

  <address class="address" style="font-style:normal">
    27 Harrow Lane<br>
    London, NW6 4QT<br>
    <span class="address__web">www.oakridgeinteriors.co.uk</span>
  </address>
</section>

</body>
</html>
```